High end Electrical/home automation Business Card

Need a card for a high end electrical and home automation company utilising the existing logo.
Phone
Email
Website

Like black look with raised detail. Don’t necessarily need to keep colour of logo it could be made grayscale or white etc

Target Market(s)

High end clients

Contact Information for Business Card

Brightmoor Electrical

Requirements
Must have
• Logo, phone, email, website, address

High end look
Nice to have
• Black background card
Raised font
Should not have
• Lots of colour

```html
<!DOCTYPE html>
<html lang="en">
<head>
<meta charset="utf-8">
<title>Brightmoor Electrical – Business Card</title>
<link href="https://fonts.googleapis.com/css2?family=Arimo:wght@400;700&family=Roboto+Condensed:wght@400;700&display=swap" rel="stylesheet">
<style>
  :root {
    --canvas: #9b9b9b;
    --card: #151515;
    --card-edge: #0b0b0b;
    --ink: #8d8d8d;
    --ink-soft: #7a7a7a;
    --ink-bright: #a4a4a4;
  }
  * { box-sizing: border-box; margin: 0; padding: 0; }
  html, body { width: 1200px; height: 1050px; overflow: hidden; }
  body {
    background: var(--canvas);
    font-family: "Roboto Condensed", "Arial Narrow", sans-serif;
    position: relative;
  }
  .card {
    position: absolute;
    left: 220px;
    width: 760px;
    height: 434px;
    background: var(--card);
    border-bottom: 3px solid var(--card-edge);
    box-shadow: 0 18px 40px rgba(0,0,0,.35);
  }
  .card--front { top: 70px; }
  .card--back { top: 546px; }

  /* front */
  .brand-mark {
    position: absolute;
    left: 70px;
    top: 176px;
    display: flex;
    align-items: center;
    gap: 14px;
  }
  .brand-mark__dot {
    width: 34px; height: 34px;
    border-radius: 50%;
    background: var(--ink);
  }
  .brand-mark__name {
    font-family: "Arimo", Arial, sans-serif;
    font-weight: 700;
    font-size: 24px;
    color: var(--ink);
    line-height: 1.15;
  }
  .contact {
    position: absolute;
    left: 390px;
    top: 96px;
    color: var(--ink);
    text-shadow: 0 1px 0 rgba(255,255,255,.08), 0 -1px 0 rgba(0,0,0,.6);
  }
  .contact__name {
    font-weight: 700;
    font-size: 27px;
    letter-spacing: 2px;
    color: var(--ink-bright);
  }
  .contact__role { font-size: 17px; color: var(--ink-soft); margin-bottom: 16px; }
  .contact__address { font-size: 18px; line-height: 1.3; margin-bottom: 14px; }
  .contact__list { list-style: none; font-size: 18px; line-height: 1.35; }
  .contact__list li { display: flex; align-items: center; gap: 9px; }
  .contact__list svg { width: 14px; height: 14px; fill: var(--ink-soft); flex: none; }

  /* back */
  .wordmark {
    position: absolute;
    left: 0; right: 0;
    top: 170px;
    display: flex;
    justify-content: center;
    align-items: center;
    gap: 18px;
  }
  .wordmark__dot {
    width: 40px; height: 40px;
    border-radius: 50%;
    background: var(--ink);
  }
  .wordmark__name {
    font-family: "Arimo", Arial, sans-serif;
    font-weight: 700;
    font-size: 50px;
    color: var(--ink);
  }
</style>
</head>
<body>
  <section class="card card--front">
    <div class="brand-mark">
      <span class="brand-mark__dot"></span>
      <span class="brand-mark__name">Brightmoor<br>Electrical</span>
    </div>
    <div class="contact">
      <p class="contact__name">DANIEL HARPER</p>
      <p class="contact__role">President</p>
      <p class="contact__address">Brightmoor Electrical LLC<br>4120 Larkspur Court<br>Juneau, Alaska 99801</p>
      <ul class="contact__list">
        <li><svg viewBox="0 0 16 16" aria-hidden="true"><path d="M3.6 1.2l2.3 2.7-1.3 1.9c.9 2 2.6 3.7 4.6 4.6l1.9-1.3 2.7 2.3-1.2 2.4C7.4 13.6 2.4 8.6 1.2 2.4z"/></svg>555-014-2287</li>
        <li><svg viewBox="0 0 16 16" aria-hidden="true"><path d="M1 3h14v10H1zM2.5 4.5v.4L8 8.8l5.5-3.9v-.4z"/></svg>info@brightmoorelectrical.com</li>
        <li><svg viewBox="0 0 16 16" aria-hidden="true"><path d="M8 1a7 7 0 100 14A7 7 0 008 1zm0 2a5 5 0 110 10A5 5 0 018 3z"/></svg>brightmoorelectrical.com</li>
      </ul>
    </div>
  </section>

  <section class="card card--back">
    <div class="wordmark">
      <span class="wordmark__dot"></span>
      <span class="wordmark__name">Brightmoor Electrical</span>
    </div>
  </section>
</body>
</html>
```